Business Card for Polygraph business in Africa

Business Card . Polygraph Examiner based in Tanzania, East Africa.
Business Card will be used to disseminate contact information to potential clients.
It should convey that I am a professional specifically in the polygraph field and perform my work with integrity.

I have attached the business card that I'm currently using, which I threw together myself initially. It's not professional enough.

Target Market(s)

Banks, Accounting Firms, Government Ministries, Gas, Oil, & Gemstone Mining Concerns, Wildlife Conservation NGOs, International companies located in East Africa.

Industry/Entity Type

Business

Contact Information for Business Card

Veritrace Kilonga
Miriam Holloway
PO Box 48317
Arusha, Tanzania
+255 612 839 274
miriamholloway@postvale.example

Colors
00a990
f37122
faa54b

Requirements
Must have
• - Veritrace Kilonga (with the word "Polygraph" being more prominent than the word "Tanzania")
• - Forensic Examinations
• - Employment Screening
• - Should contain a logo of the Continental Truthline Society (of which I'm a member)
• - I would like an accent design (such as the polygraph "squiggles" of a cardio tracing or such as that)
• - My contact information (less prominent, but large enough to read legibly). I would also consider putting the contact information on the second side of the card.
Nice to have
• My color suggestions are changeable.
Should not have
• Anything "cutesy" or "cartoonish"

```html
<!DOCTYPE html>
<html lang="en">
<head>
<meta charset="utf-8">
<title>Veritrace Kilonga – Business Card</title>
<link rel="stylesheet" href="https://fonts.googleapis.com/css2?family=Cinzel:wght@400;700&family=Open+Sans:wght@400;600&display=swap">
<style>
  :root {
    --teal: #00a990;
    --orange: #faa54b;
    --orange-deep: #f37122;
    --paper: #efefef;
    --white: #ffffff;
    --ink: #2b2b2b;
    --navy: #2e2f6b;
    --backdrop: #e4e1dc;
  }
  * { box-sizing: border-box; margin: 0; padding: 0; }
  html, body {
    width: 1200px;
    height: 900px;
    overflow: hidden;
    background: var(--backdrop);
  }
  .sheet {
    width: 1200px;
    height: 900px;
    display: flex;
    flex-direction: column;
    align-items: center;
    justify-content: center;
    gap: 40px;
  }
  .card {
    position: relative;
    width: 700px;
    height: 400px;
    overflow: hidden;
    box-shadow: 0 6px 18px rgba(0,0,0,0.18);
  }

  /* Front */
  .card--front { background: var(--teal); color: var(--white); }
  .member-badge {
    position: absolute;
    left: 70px;
    top: 110px;
    width: 180px;
    height: 180px;
  }
  .front-identity {
    position: absolute;
    left: 300px;
    top: 120px;
    width: 340px;
  }
  .front-identity .brand-name {
    font-family: "Cinzel", serif;
    font-weight: 400;
    font-size: 38px;
    line-height: 1.1;
    color: var(--white);
    padding-bottom: 10px;
    border-bottom: 2px solid var(--white);
  }
  .services {
    margin-top: 26px;
    padding-left: 60px;
    font-family: "Open Sans", sans-serif;
    font-size: 20px;
    line-height: 1.35;
  }

  /* Back */
  .card--back { background: var(--paper); }
  .back-band {
    position: absolute;
    left: 0;
    right: 0;
    top: 40px;
    height: 150px;
    background: var(--teal);
  }
  .mark-dot {
    position: absolute;
    left: 290px;
    top: 55px;
    width: 120px;
    height: 120px;
  }
  .back-brand {
    position: absolute;
    top: 208px;
    left: 0;
    right: 0;
    text-align: center;
    font-family: "Cinzel", serif;
    font-weight: 400;
    font-size: 30px;
    color: var(--teal);
  }
  .contact {
    position: absolute;
    top: 262px;
    right: 360px;
    text-align: right;
    font-family: "Open Sans", sans-serif;
    font-size: 17px;
    color: var(--ink);
    line-height: 28px;
  }
  .contact-row { display: flex; align-items: center; justify-content: flex-end; gap: 8px; }
  .contact-row svg { width: 16px; height: 16px; flex: none; }
  .divider {
    position: absolute;
    left: 370px;
    top: 262px;
    width: 2px;
    height: 52px;
    background: var(--orange);
  }
  .holder {
    position: absolute;
    left: 386px;
    top: 262px;
  }
  .holder-name {
    font-family: "Cinzel", serif;
    font-weight: 700;
    font-size: 20px;
    color: var(--teal);
    line-height: 26px;
  }
  .holder-role {
    font-family: "Open Sans", sans-serif;
    font-size: 14px;
    color: var(--ink);
  }
  .address-band {
    position: absolute;
    left: 0;
    right: 0;
    bottom: 0;
    height: 62px;
    background: var(--orange);
    color: var(--white);
    font-family: "Open Sans", sans-serif;
    font-size: 17px;
    display: flex;
    align-items: center;
    justify-content: center;
  }
</style>
</head>
<body>
<main class="sheet">

  <section class="card card--front" aria-label="Business card front">
    <svg class="member-badge" viewBox="0 0 180 180" role="img" aria-label="Continental Truthline Society member badge">
      <circle cx="90" cy="90" r="88" fill="var(--white)"/>
      <circle cx="90" cy="90" r="80" fill="none" stroke="var(--navy)" stroke-width="5"/>
      <circle cx="90" cy="90" r="62" fill="none" stroke="var(--navy)" stroke-width="2"/>
    </svg>
    <div class="front-identity">
      <div class="brand-name">Veritrace Kilonga</div>
      <div class="services">
        <p>Forensic Examinations</p>
        <p>Employment Screening</p>
      </div>
    </div>
  </section>

  <section class="card card--back" aria-label="Business card back">
    <div class="back-band"></div>
    <svg class="mark-dot" viewBox="0 0 120 120" aria-hidden="true">
      <circle cx="60" cy="60" r="58" fill="var(--white)"/>
      <circle cx="60" cy="60" r="48" fill="var(--teal)"/>
    </svg>
    <div class="back-brand">Veritrace Kilonga</div>

    <div class="contact">
      <div class="contact-row">
        <span>+255 612 839 274</span>
        <svg viewBox="0 0 24 24" aria-hidden="true"><path fill="var(--teal)" d="M6.6 10.8a15.1 15.1 0 0 0 6.6 6.6l2.2-2.2c.3-.3.7-.4 1-.2 1.1.4 2.3.6 3.6.6.6 0 1 .4 1 1V20c0 .6-.4 1-1 1A17 17 0 0 1 3 4c0-.6.4-1 1-1h3.5c.6 0 1 .4 1 1 0 1.3.2 2.5.6 3.6.1.3 0 .7-.2 1z"/></svg>
      </div>
      <div class="contact-row">
        <span>miriamholloway@postvale.example</span>
        <svg viewBox="0 0 24 24" aria-hidden="true"><rect x="2" y="5" width="20" height="14" rx="1" fill="var(--teal)"/><path d="M3 6l9 7 9-7" fill="none" stroke="var(--white)" stroke-width="1.6"/></svg>
      </div>
    </div>
    <div class="divider"></div>
    <div class="holder">
      <div class="holder-name">Miriam Holloway</div>
      <div class="holder-role">Owner</div>
    </div>

    <div class="address-band">PO Box 48317 Arusha, Tanzania</div>
  </section>

</main>
</body>
</html>
```